Corvane Business Cards

Front of business card will have logo, name, address, & telephone number. Back of card will have a list of services provided - Roads, Substation Pads, Temporary Pads, Site Pads, Land Leveling, Powerline Row Cleaning, Land Clearing, Gates, Fencing, Construction Entrances, Excavation, Trenching, Underground Utilities, Directional Boring, Pile Driving. We are a construction company that uses heavy equipment like bulldozers, motor graders/blades, dump trucks, backhoes, hydro axes, & skid loaders. We build roads, pads, & install electric utility lines & waterlines underground. This logo is new. The word "Construction" can be smaller as uploaded 2 example edited logos. We will be using this card design for many employees.
Target Market(s)
Industrial Electric Powerline, Wind Turbine, Solar Panel, & Water Utility companies.
Contact Information for Business Card
Name/Position - Dwayne Halster - Owner
Address: 4875 FM 309
Dalworth, TX 79412
Phone number - (325) 482-5096

```html
<!DOCTYPE html>
<html lang="en">
<head>
<meta charset="utf-8">
<title>Corvane Construction – Business Cards</title>
<link href="https://fonts.googleapis.com/css2?family=Poppins:wght@400;600;800&display=swap" rel="stylesheet">
<style>
  :root {
    --backdrop: #8e8e8e;
    --card: #f6f6f4;
    --maroon: #4a1620;
    --ink: #3a3a3a;
    --rule: #9a9a9a;
  }
  * { box-sizing: border-box; margin: 0; padding: 0; }
  html, body {
    width: 1200px; height: 848px; overflow: hidden;
    background: var(--backdrop);
    font-family: "Poppins", sans-serif;
  }
  .canvas {
    width: 1200px; height: 848px;
    display: flex; align-items: center; justify-content: center; gap: 40px;
  }
  .card {
    width: 560px; height: 320px;
    background: var(--card);
    border-radius: 4px;
    box-shadow: 0 8px 24px rgba(0,0,0,0.18);
    position: relative;
    overflow: hidden;
  }
  /* Front */
  .card-front { display: flex; align-items: center; }
  .brand {
    width: 250px; padding-left: 42px;
    color: var(--maroon); font-weight: 800;
    display: flex; align-items: center; gap: 12px;
  }
  .brand-mark { width: 16px; height: 16px; background: var(--maroon); flex: none; }
  .brand-name { font-size: 30px; line-height: 1; letter-spacing: 1px; text-transform: uppercase; }
  .brand-name small { display: block; font-size: 15px; letter-spacing: 2.4px; margin-top: 6px; }
  .divider { width: 1px; height: 120px; background: var(--rule); flex: none; }
  .contact { padding-left: 26px; color: var(--ink); font-size: 13px; line-height: 1.45; }
  .contact-name { color: var(--maroon); font-weight: 800; font-size: 17px; text-transform: uppercase; letter-spacing: 0.5px; line-height: 1.2; }
  .contact-role { margin-bottom: 6px; }
  .contact-line { display: flex; align-items: center; gap: 7px; white-space: nowrap; }
  .contact-line svg { width: 11px; height: 11px; fill: var(--maroon); flex: none; }
  .address { margin-bottom: 2px; }
  /* Back */
  .card-back { display: flex; align-items: center; padding-left: 70px; }
  .services { list-style: none; color: var(--ink); font-size: 12.5px; line-height: 18px; }
  .services li { display: flex; align-items: center; gap: 9px; }
  .services li::before {
    content: ""; width: 6px; height: 6px; background: var(--maroon); flex: none;
  }
</style>
</head>
<body>
<main class="canvas">
  <section class="card card-front" aria-label="Business card front">
    <div class="brand">
      <span class="brand-mark"></span>
      <div class="brand-name">Corvane<small>Construction</small></div>
    </div>
    <div class="divider"></div>
    <div class="contact">
      <div class="contact-name">Dwayne Halster</div>
      <div class="contact-role">Owner</div>
      <div class="address">4875 FM 309<br>Dalworth, TX 79412</div>
      <div class="contact-line">
        <svg viewBox="0 0 24 24" aria-hidden="true"><path d="M6.6 10.8a15.1 15.1 0 0 0 6.6 6.6l2.2-2.2a1 1 0 0 1 1-.25 11.4 11.4 0 0 0 3.6.57 1 1 0 0 1 1 1V20a1 1 0 0 1-1 1A17 17 0 0 1 3 4a1 1 0 0 1 1-1h3.5a1 1 0 0 1 1 1c0 1.250.2 2.450.57 3.57a1 1 0 0 1-.25 1z"/></svg>
        <span>(325) 482-5096</span>
      </div>
      <div class="contact-line">
        <svg viewBox="0 0 24 24" aria-hidden="true"><path d="M2 5h20v14H2z M2 5l10 8 10-8" fill="none" stroke="#4a1620" stroke-width="2.4"/></svg>
        <span>info@corvaneconstruction.com</span>
      </div>
      <div class="contact-line">
        <svg viewBox="0 0 24 24" aria-hidden="true"><circle cx="12" cy="12" r="10"/></svg>
        <span>corvaneconstruction.com</span>
      </div>
    </div>
  </section>

  <section class="card card-back" aria-label="Business card back">
    <ul class="services">
      <li>Roads</li>
      <li>Substation Pads</li>
      <li>Temporary Pads</li>
      <li>Site Pads</li>
      <li>Land Leveling</li>
      <li>Powerline Row Cleaning</li>
      <li>Land Clearing</li>
      <li>Gates</li>
      <li>Fencing</li>
      <li>Construction Entrances</li>
      <li>Excavation</li>
      <li>Trenching</li>
      <li>Underground Utilities</li>
      <li>Directional Boring</li>
      <li>Pile Driving</li>
    </ul>
  </section>
</main>
</body>
</html>
```